Business card for marketing analytics company

Need a business card for new company. I have a logo already that I want to be built into the card and should use those colours

Company is called steered by tallies
Design must bring steered by tallies to life not be a card that could be for anyone with a logo put on it.

Like the front to be fairly clean and uncluttered bringing the logo out with a suitable design on the back of the card.

The logo represents a compass and business growth so those themes along with numbers, analytics , data are appropriate.
I'm often working with creative industries so also needs to reflect the creative side of analytics rather than be very corporate looking.

Target Market(s)

Ad agency, media agency, consumer goods clients

Industry/Entity Type

Market Research

Contact Information for Business Card

Needs to include name, title, email and phone number

Colors
f78f20
f68d4d
ec1f27

Requirements
Must have
• Must bring steered by tallies to life not be a card that could be for anyone with a logo put on it.
• Logo, Correct colours
• Like a design on the back that relates to company name
• Designs for both sides
Should not have
• Please do not just submit logo and a coloured card.
• It needs to have a design element to it
• No black background
• No clear cards - needs front & back

```html
<!DOCTYPE html>
<html lang="en">
<head>
<meta charset="utf-8">
<title>Steered by Tallies — Business Card</title>
<link href="https://fonts.googleapis.com/css2?family=Lato:wght@400;700;900&display=swap" rel="stylesheet">
<style>
  :root {
    --stage: #2b2b2b;
    --red: #c41a21;
    --red-deep: #a8141a;
    --orange: #f15a24;
    --orange-soft: #f68d4d;
    --white: #ffffff;
    --silver: #cfcfcf;
    --ink: #222222;
    --chart-fill: #efefef;
  }
  * { margin: 0; padding: 0; box-sizing: border-box; }
  html, body {
    width: 1200px; height: 997px; overflow: hidden;
    background: var(--stage);
    font-family: "Lato", sans-serif;
  }
  .canvas { position: relative; width: 1200px; height: 997px; }

  .card { position: absolute; top: 382px; width: 507px; height: 305px; overflow: hidden; }
  .card--front { left: 80px; background: linear-gradient(100deg, var(--silver) 0%, #eeeeee 30%, var(--white) 55%); }
  .card--back { left: 631px; background: var(--red); }

  .brand { position: absolute; display: flex; align-items: center; gap: 12px; }
  .brand__mark { width: 58px; height: 58px; border-radius: 50%; border: 3px solid var(--red); flex: none; }
  .brand__name { font-weight: 700; font-size: 19px; line-height: 1.1; }
  .card--front .brand { left: 22px; top: 18px; }
  .card--front .brand__name { color: var(--ink); }
  .card--back .brand { left: 18px; top: 16px; }
  .card--back .brand__mark { border-color: var(--white); }
  .card--back .brand__name { color: var(--white); }
  .brand__line--indent { padding-left: 28px; display: block; }

  .info-band { position: absolute; left: 0; top: 161px; width: 100%; height: 144px; }
  .info-band svg { position: absolute; inset: 0; }

  .contact { position: absolute; color: var(--white); }
  .contact__name { left: 32px; top: 187px; font-weight: 900; font-size: 16px; letter-spacing: 0.2px; }
  .contact__title { left: 32px; top: 206px; font-size: 11px; }
  .contact__phone { left: 32px; top: 247px; font-size: 12px; }
  .contact__email { left: 32px; top: 266px; font-size: 12px; }
  .contact__web { right: 24px; top: 267px; font-weight: 700; font-size: 12px; }

  .back-art { position: absolute; inset: 0; }
</style>
</head>
<body>
<main class="canvas">

  <section class="card card--front" aria-label="Card front">
    <div class="brand">
      <span class="brand__mark"></span>
      <span class="brand__name">Steered by<span class="brand__line--indent">Tallies</span></span>
    </div>

    <div class="info-band">
      <svg width="507" height="144" viewBox="0 0 507 144">
        <rect x="0" y="0" width="507" height="4" fill="var(--red)"/>
        <rect x="0" y="9" width="507" height="126" fill="var(--red)"/>
        <rect x="0" y="138" width="507" height="6" fill="var(--red)"/>
        <polygon points="33,9 49,9 41,18" fill="var(--white)"/>
        <path role="img" aria-label="Faint number-filled growth line" d="M150 105 L245 68 L300 102 L385 60 L460 30 L507 20" fill="none" stroke="var(--red-deep)" stroke-width="22" stroke-linecap="round" stroke-linejoin="round" opacity="0.7"/>
      </svg>
    </div>

    <p class="contact contact__name">MAYA THORNTON</p>
    <p class="contact contact__title">Director</p>
    <p class="contact contact__phone">08412937406</p>
    <p class="contact contact__email">mthornton@tallyline.com.au</p>
    <p class="contact contact__web">www.tallyline.com.au</p>
  </section>

  <section class="card card--back" aria-label="Card back">
    <svg class="back-art" width="507" height="305" viewBox="0 0 507 305">
      <defs>
        <linearGradient id="growth-fill" x1="0" y1="0" x2="1" y2="1">
          <stop offset="0" stop-color="var(--orange)"/>
          <stop offset="1" stop-color="#e9531f"/>
        </linearGradient>
      </defs>
      <polygon points="0,212 100,276 216,156 294,216 418,78 507,150 507,305 0,305" fill="url(#growth-fill)"/>
      <g role="img" aria-label="Growth line chart filled with scattered numbers" fill="var(--chart-fill)">
        <polyline points="0,190 100,254 216,131 294,193 418,55 507,130" fill="none" stroke="var(--chart-fill)" stroke-width="30" stroke-linejoin="round"/>
        <circle cx="18" cy="188" r="32"/>
        <circle cx="100" cy="254" r="32"/>
        <circle cx="216" cy="131" r="32"/>
        <circle cx="294" cy="193" r="32"/>
        <circle cx="418" cy="55" r="32"/>
      </g>
    </svg>
    <div class="brand">
      <span class="brand__mark"></span>
      <span class="brand__name">Steered by<span class="brand__line--indent">Tallies</span></span>
    </div>
  </section>

</main>
</body>
</html>
```